Business Card for Vorla Parts Wholesale supplier

Hi There! I need a new business card for our company. We are specialized in selling Vorla parts, mostly we sell new LCD screens for Zelnar and Drelks. I would like to see that back in the design.

You can find the colors and logo's on our website: www.hartuvo.nl

Industry/Entity Type

Business

Contact Information for Business Card

My Details:
Tobias Lindqvist

Phone: 0031687203316
E-mail: Tobias@hartuvo.nl

Slogan: "Because Quality Matters"

Font styles to use
Sans Serif

Colors

Designer to choose colors to be used in the design.

Requirements
Must have
• A Black backside with the Hartuvo logo on it. The front side should be clean with only my contact details.
• But I'm also open for something really different or awesome!
Nice to have
• Remember that we are in the parts & repairing industry, So i'll be handing those business cards mainly to repair companies. Maybe you can do something with that thought :)

```html
<!DOCTYPE html>
<html lang="en">
<head>
<meta charset="utf-8">
<title>Hartuvo Business Card</title>
<link rel="stylesheet" href="https://fonts.googleapis.com/css2?family=Open+Sans:wght@400;600;700&display=swap">
<style>
  :root {
    --backdrop: #5b4a3c;
    --card-black: #000000;
    --card-white: #ffffff;
    --accent: #f47321;
    --text-grey: #555555;
    --text-white: #ffffff;
  }
  * { margin: 0; padding: 0; box-sizing: border-box; }
  html, body {
    width: 1200px;
    height: 987px;
    overflow: hidden;
    background: var(--backdrop);
    font-family: "Open Sans", Arial, sans-serif;
  }
  .card {
    position: absolute;
    width: 615px;
    height: 352px;
    overflow: hidden;
    box-shadow: 0 2px 4px rgba(0,0,0,0.35);
  }
  .card-front { left: 293px; top: 130px; background: var(--card-white); }
  .card-back { left: 292px; top: 505px; background: var(--card-black); }

  .front-brand {
    position: absolute;
    left: 0; top: 0;
    width: 306px; height: 100%;
    background: var(--card-black);
    display: flex;
    align-items: center;
    justify-content: center;
    gap: 12px;
  }
  .brand-square {
    width: 34px; height: 34px;
    background: var(--accent);
  }
  .brand-name {
    color: var(--text-white);
    font-weight: 700;
    font-size: 44px;
    letter-spacing: 0.5px;
    line-height: 1;
  }
  .front-stripe {
    position: absolute;
    right: 0; top: 0;
    width: 16px; height: 100%;
    background: var(--accent);
  }
  .contact {
    position: absolute;
    left: 360px;
    top: 115px;
  }
  .contact-name {
    color: var(--accent);
    font-weight: 600;
    font-size: 20px;
    letter-spacing: 0.3px;
    margin-bottom: 14px;
  }
  .contact-list { list-style: none; }
  .contact-item {
    display: flex;
    align-items: center;
    gap: 7px;
    color: var(--text-grey);
    font-size: 15px;
    line-height: 23px;
  }
  .contact-icon { width: 14px; height: 14px; fill: var(--accent); flex: none; }

  .back-brand {
    position: absolute;
    left: 0; right: 0;
    top: 130px;
    text-align: center;
    color: var(--accent);
    font-weight: 700;
    font-size: 60px;
    line-height: 1;
  }
  .slogan {
    position: absolute;
    left: 0; right: 0;
    top: 278px;
    text-align: center;
    color: var(--text-white);
    font-weight: 600;
    font-size: 19px;
  }
</style>
</head>
<body>
  <section class="card card-front">
    <div class="front-brand">
      <span class="brand-square"></span>
      <span class="brand-name">hartuvo</span>
    </div>
    <div class="contact">
      <h1 class="contact-name">TOBIAS LINDQVIST</h1>
      <ul class="contact-list">
        <li class="contact-item">
          <svg class="contact-icon" viewBox="0 0 16 16" aria-hidden="true"><path d="M3.6 1.2l2.3 2.6c.4.4.4 1 0 1.4L4.8 6.4c.9 2 2.6 3.8 4.8 4.8l1.2-1.1c.4-.4 1-.4 1.4 0l2.6 2.3c.4.4.4 1 0 1.4l-1.4 1.3C11.6 16.9 1 7 1.9 3.2L3.2 1.2c.1-.2.3-.1.4 0z"/></svg>
          0031687203316
        </li>
        <li class="contact-item">
          <svg class="contact-icon" viewBox="0 0 16 16" aria-hidden="true"><path d="M1 3h14v1.2L8 8.6 1 4.2z"/><path d="M1 5.6l7 4.4 7-4.4V13H1z"/></svg>
          Tobias@hartuvo.nl
        </li>
        <li class="contact-item">
          <svg class="contact-icon" viewBox="0 0 16 16" aria-hidden="true"><circle cx="8" cy="8" r="7"/><path d="M4 4.5c1.5.3 2.6 1 2.4 2.3-.2 1-1.6 1-1.4 2.4.1 1 1 1.4 1 2.8M10.5 2.6c-.6 1 0 2 1.2 2.2 1 .2 1.6 1 1.2 2.2" stroke="#fff" stroke-width="1.2" fill="none"/></svg>
          www.hartuvo.nl
        </li>
      </ul>
    </div>
    <div class="front-stripe"></div>
  </section>

  <section class="card card-back">
    <div class="back-brand">hartuvo</div>
    <p class="slogan">Because Quality Matters</p>
  </section>
</body>
</html>
```